Nivel Crest - Powerpoint Templates

We are a consultancy to help builders to optimize their planning in order to save building costs. For that reason we need templates for teasers and presentations where we offer our services, show our team and their capacities and present workflows, organization charts, price lists etc.

```html
<!DOCTYPE html>
<html lang="en">
<head>
<meta charset="utf-8">
<title>Nivel Crest – Presentation Template</title>
<link href="https://fonts.googleapis.com/css2?family=Montserrat:wght@400;500;600;700;800&display=swap" rel="stylesheet">
<style>
:root{
  --bg:#d6d6d6;
  --paper:#ffffff;
  --gold:#c8902e;
  --gold-dark:#a9741f;
  --gold-light:#e8c46a;
  --ink:#2b2b2b;
  --muted:#555;
  --grey:#a3a3a5;
  --line:#d9b779;
}
*{margin:0;padding:0;box-sizing:border-box}
html,body{width:772px;height:1200px;overflow:hidden;background:var(--bg);font-family:'Montserrat',sans-serif;color:var(--ink)}
.board{position:relative;width:772px;height:1200px}
.slide{position:absolute;width:287px;height:179px;background:var(--paper);overflow:hidden}
.abs{position:absolute}
.photo{position:absolute;background:linear-gradient(100deg,#c58c2c 0%,#e2b75a 30%,#8ea27c 55%,#b07a3a 75%,#7a4a1e 100%)}
.photo.soft{background:linear-gradient(100deg,#c8912e 0%,#e6c46c 45%,#b07a38 80%,#6e421c 100%)}
.photo.office{background:linear-gradient(160deg,#d8dde2,#8e98a4 60%,#3e4650)}
.photo.tech{background:linear-gradient(160deg,#b9d5ea,#5f8fb5 55%,#243a56)}
.photo.desk{background:linear-gradient(160deg,#e6e9ee,#9aa3ad 50%,#2d3340)}
.photo.map{background:linear-gradient(160deg,#e9eff6,#cbd8e8)}
.brand{font-weight:700;color:var(--gold);letter-spacing:.5px;text-transform:uppercase;white-space:nowrap}
.brand .dot{display:inline-block;width:9px;height:9px;background:var(--gold);margin-right:4px;vertical-align:-1px}
.heading{color:var(--gold);font-weight:500;font-size:8.5px;white-space:nowrap}
.title{color:var(--gold);font-weight:600;font-size:5.5px}
.body{font-size:3.8px;line-height:1.25;color:var(--ink)}
.bullets{list-style:none}
.bullets li{position:relative;padding-left:6px;margin-bottom:4px;font-size:3.8px;line-height:1.25}
.bullets li::before{content:"";position:absolute;left:0;top:1px;width:2px;height:2px;border-radius:50%;background:var(--gold)}
.footer .brand{position:absolute;left:10px;top:165px;font-size:4.5px}
.footer .brand .dot{width:6px;height:6px;margin-right:2px}
.footer .rule{position:absolute;left:60px;right:44px;top:168px;height:.5px;background:var(--line)}
.footer .page{position:absolute;right:10px;top:166px;font-size:3.3px;color:var(--ink)}
.footer .page b{color:var(--gold);font-weight:600}
.icon{position:absolute;width:10px;height:10px}
.white{color:#fff}
.center{text-align:center}
table{border-collapse:collapse;width:100%;font-size:3.6px}
th{background:var(--grey);color:#fff;font-weight:500;height:13px;text-align:center;line-height:1.1}
th:first-child{text-align:left;padding-left:2px}
td{height:12px;border-bottom:.5px solid #ccc;text-align:center}
td:first-child{text-align:left;padding-left:2px}
th.hl{background:var(--gold)}
</style>
</head>
<body>
<svg width="0" height="0" style="position:absolute">
  <defs>
    <symbol id="person-badge" viewBox="0 0 20 20">
      <circle cx="10" cy="10" r="10" fill="#c8902e"/>
      <circle cx="10" cy="6.5" r="2.6" fill="#fff"/>
      <path d="M5 15.5c0-3 2.2-5 5-5s5 2 5 5z" fill="#fff"/>
    </symbol>
    <symbol id="person-ring" viewBox="0 0 20 20">
      <circle cx="10" cy="10" r="9" fill="none" stroke="#fff" stroke-width="1"/>
      <circle cx="10" cy="7" r="2.4" fill="#fff"/>
      <path d="M5.6 14.8c0-2.8 2-4.6 4.4-4.6s4.4 1.8 4.4 4.6z" fill="#fff"/>
    </symbol>
  </defs>
</svg>

<main class="board">

  <!-- Cover -->
  <section class="slide" style="left:79px;top:78px">
    <div class="brand abs" style="left:15px;top:14px;font-size:8px"><span class="dot"></span>Nivel Crest</div>
    <div class="photo" style="left:0;top:36px;width:287px;height:122px" role="img" aria-label="Excavator at a construction site under a golden sky"></div>
    <h1 class="abs white" style="left:15px;top:77px;font-size:14.5px;font-weight:700;line-height:1.05">PRESENTATION<br>TITLE GOES HERE</h1>
    <p class="abs white" style="left:15px;top:113px;font-size:5.5px">Subtitle of Presentation Goes Here</p>
    <p class="abs white" style="left:15px;top:132px;font-size:4.5px">Friday, July 08, 2023</p>
    <p class="abs center" style="left:0;width:287px;top:165px;font-size:4.5px;color:var(--muted)">© Copyright Nivel Crest All Right Reserved</p>
  </section>

  <!-- Intro with services list -->
  <section class="slide" style="left:405px;top:78px">
    <div class="photo" style="left:12px;top:14px;width:263px;height:60px" role="img" aria-label="Construction machinery and city skyline"></div>
    <h2 class="abs white" style="left:38px;top:23px;font-size:8px;font-weight:500">Heading Goes Here</h2>
    <p class="abs body white" style="left:38px;top:33px;width:152px;font-size:3.4px">Lorem ipsum dolor sit amet, consectetuer adipiscing elit, sed diam nonummy nibh euismod tincidunt ut laoreet dolore magna aliquam erat volutpat. Ut wisi enim ad minim veniam, quis nostrud exerci tation ullamcorper suscipit lobortis nisl ut aliquip ex ea commodo consequat.</p>
    <h3 class="abs title" style="left:14px;top:87px">Title Goes Here</h3>
    <ul class="abs bullets" style="left:14px;top:98px;width:115px">
      <li>Lorem ipsum dolor sit amet, consectetuer adipiscing elit, sed diam nonummy nibh euismod tincidunt ut laoreet dolore magna aliquam erat volutpat. Ut wisi enim ad minim veniam, quis nostrud exerci tation</li>
      <li>Lorem ipsum dolor sit amet, consectetuer adipiscing elit, sed diam nonummy nibh euismod tincidunt ut laoreet dolore magna aliquam erat volutpat. Ut wisi enim ad minim veniam, quis nostrud exerci tation</li>
    </ul>
    <svg class="icon" style="left:155px;top:97px"><use href="#person-badge"/></svg>
    <svg class="icon" style="left:155px;top:114px"><use href="#person-badge"/></svg>
    <svg class="icon" style="left:155px;top:132px"><use href="#person-badge"/></svg>
    <svg class="icon" style="left:222px;top:97px"><use href="#person-badge"/></svg>
    <svg class="icon" style="left:222px;top:114px"><use href="#person-badge"/></svg>
    <svg class="icon" style="left:222px;top:132px"><use href="#person-badge"/></svg>
    <p class="abs" style="left:170px;top:100px;font-size:4.5px">Title Goes Here</p>
    <p class="abs" style="left:170px;top:117px;font-size:4.5px">Title Goes Here</p>
    <p class="abs" style="left:170px;top:135px;font-size:4.5px">Title Goes Here</p>
    <p class="abs" style="left:237px;top:100px;font-size:4.5px">Title Goes Here</p>
    <p class="abs" style="left:237px;top:117px;font-size:4.5px">Title Goes Here</p>
    <p class="abs" style="left:237px;top:135px;font-size:4.5px">Title Goes Here</p>
    <div class="footer"><div class="brand"><span class="dot"></span>Nivel Crest</div><div class="rule"></div><div class="page">NIVEL CREST | <b>01</b></div></div>
  </section>

  <!-- Map and pie -->
  <section class="slide" style="left:79px;top:290px">
    <h2 class="abs heading" style="left:15px;top:13px">Heading Goes Here</h2>
    <h3 class="abs title" style="left:15px;top:45px">Title Goes Here</h3>
    <ul class="abs bullets" style="left:15px;top:56px;width:145px">
      <li>Lorem ipsum dolor sit amet, consectetuer adipiscing elit, sed diam nonummy nibh euismod tincidunt ut laoreet dolore magna aliquam erat volutpat. Ut wisi enim ad minim veniam, quis nostrud exerci tation ullamcorper suscipit lobortis nisl ut aliquip ex ea commodo</li>
      <li>Lorem ipsum dolor sit amet, consectetuer adipiscing elit, sed diam nonummy nibh euismod tincidunt ut laoreet dolore magna aliquam erat volutpat. Ut wisi enim ad minim veniam, quis nostrud exerci tation ullamcorper suscipit lobortis nisl ut aliquip ex ea commodo</li>
      <li>Lorem ipsum dolor sit amet, consectetuer adipiscing elit, sed diam nonummy nibh euismod tincidunt ut laoreet dolore magna aliquam erat volutpat. Ut wisi enim ad minim veniam, quis nostrud exerci tation ullamcorper suscipit lobortis nisl ut aliquip ex ea commodo</li>
    </ul>
    <div class="photo map" style="left:181px;top:38px;width:74px;height:56px" role="img" aria-label="Map of North America with project locations"></div>
    <svg class="abs" style="left:170px;top:102px" width="62" height="38" viewBox="0 0 62 38">
      <ellipse cx="30" cy="22" rx="29" ry="15" fill="#8a4a1c"/>
      <g transform="translate(30 18) scale(1 .55) rotate(-90)">
        <circle r="14.5" fill="none" stroke="#1f6fc0" stroke-width="29" pathLength="100" stroke-dasharray="12 88"/>
        <circle r="14.5" fill="none" stroke="#e8782c" stroke-width="29" pathLength="100" stroke-dasharray="0 12 41 47"/>
        <circle r="14.5" fill="none" stroke="#a0a0a0" stroke-width="29" pathLength="100" stroke-dasharray="0 53 20 27"/>
        <circle r="14.5" fill="none" stroke="#f3b51c" stroke-width="29" pathLength="100" stroke-dasharray="0 73 27 0"/>
      </g>
      <text x="17" y="13" font-size="3" fill="#fff">27%</text>
      <text x="33" y="9" font-size="3" fill="#fff">12%</text>
      <text x="38" y="22" font-size="3" fill="#fff">41%</text>
      <text x="12" y="24" font-size="3" fill="#fff">20%</text>
    </svg>
    <div class="abs" style="left:235px;top:102px;font-size:2.6px;line-height:11.5px">
      <div><span style="color:#1f6fc0">■</span> Board &amp; Management</div>
      <div><span style="color:#e8782c">■</span> Top 20</div>
      <div><span style="color:#a0a0a0">■</span> Top 21-50</div>
      <div><span style="color:#f3b51c">■</span> Retail/Institutions/Other</div>
    </div>
    <div class="footer"><div class="brand"><span class="dot"></span>Nivel Crest</div><div class="rule"></div><div class="page">NIVEL CREST | <b>01</b></div></div>
  </section>

  <!-- Our Service -->
  <section class="slide" style="left:405px;top:290px">
    <div class="photo" style="left:0;top:0;width:287px;height:91px" role="img" aria-label="Excavator working beside city towers"></div>
    <h2 class="abs white center" style="left:0;width:287px;top:8px;font-size:9px;font-weight:400">Our <b style="font-weight:700">Service</b></h2>
    <div class="abs" style="left:118px;width:51px;top:21px;height:.5px;background:#fff"></div>
    <p class="abs body white center" style="left:50px;width:187px;top:28px;font-size:3.4px">Lorem ipsum dolor sit amet, consectetuer adipiscing elit, sed diam nonummy nibh euismod tincidunt ut laoreet dolore magna aliquam erat volutpat. Ut wisi enim ad minim veniam, quis nostrud exerci tation ullamcorper suscipit lobortis nisl ut aliquip ex ea commodo consequat. Duis autem vel eum iriure dolor in hendrerit in vulputate velit esse molestie consequat.</p>
    <svg class="abs" style="left:27px;top:63px" width="22" height="22"><use href="#person-ring"/></svg>
    <svg class="abs" style="left:80px;top:63px" width="22" height="22"><use href="#person-ring"/></svg>
    <svg class="abs" style="left:133px;top:63px" width="22" height="22"><use href="#person-ring"/></svg>
    <svg class="abs" style="left:186px;top:63px" width="22" height="22"><use href="#person-ring"/></svg>
    <svg class="abs" style="left:239px;top:63px" width="22" height="22"><use href="#person-ring"/></svg>
    <div class="abs center" style="left:11px;width:265px;top:96px;display:flex;justify-content:space-between">
      <div style="width:53px"><p style="font-size:6px;line-height:1.05">Service Title<br><span style="font-size:5px">Goes Here</span></p><p style="font-size:3.4px;margin-top:6px">Vivomus eu dull ex.<br>curobour dopibus</p></div>
      <div style="width:53px"><p style="font-size:6px;line-height:1.05">Service Title<br><span style="font-size:5px">Goes Here</span></p><p style="font-size:3.4px;margin-top:6px">Vivomus eu dull ex.<br>curobour dopibus</p></div>
      <div style="width:53px"><p style="font-size:6px;line-height:1.05">Service Title<br><span style="font-size:5px">Goes Here</span></p><p style="font-size:3.4px;margin-top:6px">Vivomus eu dull ex.<br>curobour dopibus</p></div>
      <div style="width:53px"><p style="font-size:6px;line-height:1.05">Service Title<br><span style="font-size:5px">Goes Here</span></p><p style="font-size:3.4px;margin-top:6px">Vivomus eu dull ex.<br>curobour dopibus</p></div>
      <div style="width:53px"><p style="font-size:6px;line-height:1.05">Service Title<br><span style="font-size:5px">Goes Here</span></p><p style="font-size:3.4px;margin-top:6px">Vivomus eu dull ex.<br>curobour dopibus</p></div>
    </div>
    <div class="footer"><div class="brand"><span class="dot"></span>Nivel Crest</div><div class="rule"></div><div class="page">NIVEL CREST | <b>01</b></div></div>
  </section>

  <!-- Three columns -->
  <section class="slide" style="left:79px;top:501px">
    <div class="abs" style="left:0;top:0;width:287px;height:52px;background:linear-gradient(90deg,var(--gold-dark),var(--gold-light) 55%,var(--gold-dark))"></div>
    <h2 class="abs white center" style="left:0;width:287px;top:9px;font-size:9px;font-weight:500">Heading Goes Here</h2>
    <div class="photo office" style="left:12px;top:32px;width:79px;height:38px;outline:1.5px solid #fff" role="img" aria-label="Team working in an office"></div>
    <div class="photo tech" style="left:104px;top:32px;width:79px;height:38px;outline:1.5px solid #fff" role="img" aria-label="Business person using a tablet"></div>
    <div class="photo desk" style="left:196px;top:32px;width:79px;height:38px;outline:1.5px solid #fff" role="img" aria-label="Meeting with a laptop at a desk"></div>
    <h3 class="abs title center" style="left:12px;width:79px;top:75px;font-weight:500;font-size:5.5px">Heading Goes Here</h3>
    <h3 class="abs title center" style="left:104px;width:79px;top:75px;font-weight:500;font-size:5.5px">Heading Goes Here</h3>
    <h3 class="abs title center" style="left:196px;width:79px;top:75px;font-weight:500;font-size:5.5px">Heading Goes Here</h3>
    <ul class="abs bullets" style="left:15px;top:88px;width:70px"><li>Lorem ipsum dolar sit amet, consectetur adipising edit. Vivamus eu dui ex.</li><li>Lorem ipsum dolar sit amet, consectetur adipising edit. Vivamus eu dui ex.</li><li>Lorem ipsum dolar sit amet, consectetur adipising edit. Vivamus eu dui ex.</li></ul>
    <ul class="abs bullets" style="left:107px;top:88px;width:70px"><li>Lorem ipsum dolar sit amet, consectetur adipising edit. Vivamus eu dui ex.</li><li>Lorem ipsum dolar sit amet, consectetur adipising edit. Vivamus eu dui ex.</li><li>Lorem ipsum dolar sit amet, consectetur adipising edit. Vivamus eu dui ex.</li></ul>
    <ul class="abs bullets" style="left:199px;top:88px;width:70px"><li>Lorem ipsum dolar sit amet, consectetur adipising edit. Vivamus eu dui ex.</li><li>Lorem ipsum dolar sit amet, consectetur adipising edit. Vivamus eu dui ex.</li><li>Lorem ipsum dolar sit amet, consectetur adipising edit. Vivamus eu dui ex.</li></ul>
    <div class="footer"><div class="brand"><span class="dot"></span>Nivel Crest</div><div class="rule"></div><div class="page">NIVEL CREST | <b>01</b></div></div>
  </section>

  <!-- Bar chart -->
  <section class="slide" style="left:405px;top:501px">
    <h2 class="abs heading" style="left:12px;top:12px">Heading Goes Here</h2>
    <p class="abs body" style="left:13px;top:41px;width:140px">Lorem ipsum dolor sit amet, consectetuer adipiscing elit, sed diam nonummy nibh euismod tincidunt ut laoreet dolore magna aliquam erat volutpat. Ut wisi enim ad minim veniam, quis nostrud exerci tation</p>
    <svg class="abs" style="left:10px;top:65px" width="155" height="70" viewBox="0 0 155 70">
      <defs><linearGradient id="bar-grey" x1="0" y1="0" x2="0" y2="1"><stop offset="0" stop-color="#555"/><stop offset="1" stop-color="#bbb"/></linearGradient></defs>
      <g font-size="3" fill="#333">
        <text x="2" y="3">6</text><text x="2" y="13">5</text><text x="2" y="23">4</text><text x="2" y="33">3</text><text x="2" y="43">2</text><text x="2" y="53">1</text><text x="2" y="63">0</text>
      </g>
      <g stroke="#ddd" stroke-width=".4">
        <line x1="8" y1="2" x2="153" y2="2"/><line x1="8" y1="12" x2="153" y2="12"/><line x1="8" y1="22" x2="153" y2="22"/><line x1="8" y1="32" x2="153" y2="32"/><line x1="8" y1="42" x2="153" y2="42"/><line x1="8" y1="52" x2="153" y2="52"/><line x1="8" y1="62" x2="153" y2="62"/>
      </g>
      <rect x="12" y="19" width="8" height="43" fill="#c8902e"/>
      <rect x="22" y="38" width="8" height="24" fill="url(#bar-grey)"/>
      <rect x="32" y="42" width="8" height="20" fill="url(#bar-grey)"/>
      <rect x="49" y="37" width="8" height="25" fill="url(#bar-grey)"/>
      <rect x="59" y="18" width="8" height="44" fill="#c8902e"/>
      <rect x="69" y="42" width="8" height="20" fill="url(#bar-grey)"/>
      <rect x="86" y="27" width="8" height="35" fill="url(#bar-grey)"/>
      <rect x="96" y="44" width="8" height="18" fill="url(#bar-grey)"/>
      <rect x="106" y="32" width="8" height="30" fill="#c8902e"/>
      <rect x="122" y="17" width="8" height="45" fill="#111"/>
      <rect x="132" y="34" width="8" height="28" fill="url(#bar-grey)"/>
      <rect x="142" y="12" width="8" height="50" fill="#c8902e"/>
      <g font-size="3" fill="#333" text-anchor="middle">
        <text x="26" y="68">Category 1</text><text x="63" y="68">Category 2</text><text x="100" y="68">Category 3</text><text x="136" y="68">Category 4</text>
      </g>
    </svg>
    <div class="photo desk" style="left:178px;top:27px;width:97px;height:120px" role="img" aria-label="Business person reviewing charts at a laptop"></div>
    <div class="footer"><div class="brand"><span class="dot"></span>Nivel Crest</div><div class="rule"></div><div class="page">NIVEL CREST | <b>01</b></div></div>
  </section>

  <!-- Table -->
  <section class="slide" style="left:79px;top:713px">
    <h2 class="abs heading" style="left:10px;top:11px">Heading Goes Here</h2>
    <div class="abs" style="left:92px;top:37px;width:46px;height:105px;border:.8px solid var(--gold);border-radius:3px"></div>
    <div class="abs" style="left:10px;top:40px;width:268px">
      <table>
        <tr><th style="width:82px">Heading Goes Here</th><th class="hl">Heading<br>Goes Here</th><th>Heading<br>Goes Here</th><th>Heading<br>Goes Here</th><th>Heading<br>Goes Here</th></tr>
        <tr><td>Lorem Ipsum Goes Here</td><td>23</td><td>12</td><td>78</td><td>12</td></tr>
        <tr><td>Lorem Ipsum Goes Here</td><td>45</td><td>56</td><td>12</td><td>56</td></tr>
        <tr><td>Lorem Ipsum Goes Here</td><td>78</td><td>76</td><td>34</td><td>76</td></tr>
        <tr><td>Lorem Ipsum Goes Here</td><td>22</td><td>12</td><td>55</td><td>12</td></tr>
        <tr><td>Lorem Ipsum Goes Here</td><td>34</td><td>66</td><td>45</td><td>66</td></tr>
        <tr><td>Lorem Ipsum Goes Here</td><td>67</td><td>47</td><td>78</td><td>47</td></tr>
        <tr><td>Lorem Ipsum Goes Here</td><td>87</td><td>67</td><td>12</td><td>67</td></tr>
      </table>
    </div>
    <div class="footer"><div class="brand"><span class="dot"></span>Nivel Crest</div><div class="rule"></div><div class="page">NIVEL CREST | <b>01</b></div></div>
  </section>

  <!-- Team / features grid -->
  <section class="slide" style="left:405px;top:713px">
    <h2 class="abs heading" style="left:12px;top:11px">Heading Goes Here</h2>
    <svg class="abs" style="left:12px;top:44px" width="20" height="20"><use href="#person-badge"/></svg>
    <svg class="abs" style="left:12px;top:79px" width="20" height="20"><use href="#person-badge"/></svg>
    <svg class="abs" style="left:12px;top:114px" width="20" height="20"><use href="#person-badge"/></svg>
    <svg class="abs" style="left:149px;top:44px" width="20" height="20"><use href="#person-badge"/></svg>
    <svg class="abs" style="left:149px;top:79px" width="20" height="20"><use href="#person-badge"/></svg>
    <svg class="abs" style="left:149px;top:114px" width="20" height="20"><use href="#person-badge"/></svg>
    <div class="abs" style="left:35px;top:40px;width:.5px;height:28px;background:#999"></div>
    <div class="abs" style="left:35px;top:75px;width:.5px;height:28px;background:#999"></div>
    <div class="abs" style="left:35px;top:110px;width:.5px;height:28px;background:#999"></div>
    <div class="abs" style="left:172px;top:40px;width:.5px;height:28px;background:#999"></div>
    <div class="abs" style="left:172px;top:75px;width:.5px;height:28px;background:#999"></div>
    <div class="abs" style="left:172px;top:110px;width:.5px;height:28px;background:#999"></div>
    <div class="abs" style="left:41px;top:42px;width:95px"><p style="font-size:5.5px;font-weight:500">Title Goes Here</p><p class="body">Lorem ipsum dolor sit amet, consectetuer adipiscing elit, sed diam nonummy nibh euismod tincidunt ut laoreet dolore magna</p></div>
    <div class="abs" style="left:41px;top:77px;width:95px"><p style="font-size:5.5px;font-weight:500">Title Goes Here</p><p class="body">Lorem ipsum dolor sit amet, consectetuer adipiscing elit, sed diam nonummy nibh euismod tincidunt ut laoreet dolore magna</p></div>
    <div class="abs" style="left:41px;top:113px;width:95px"><p style="font-size:5.5px;font-weight:500">Title Goes Here</p><p class="body">Lorem ipsum dolor sit amet, consectetuer adipiscing elit, sed diam nonummy nibh euismod tincidunt ut laoreet dolore magna</p></div>
    <div class="abs" style="left:178px;top:42px;width:95px"><p style="font-size:5.5px;font-weight:500">Title Goes Here</p><p class="body">Lorem ipsum dolor sit amet, consectetuer adipiscing elit, sed diam nonummy nibh euismod tincidunt ut laoreet dolore magna</p></div>
    <div class="abs" style="left:178px;top:77px;width:95px"><p style="font-size:5.5px;font-weight:500">Title Goes Here</p><p class="body">Lorem ipsum dolor sit amet, consectetuer adipiscing elit, sed diam nonummy nibh euismod tincidunt ut laoreet dolore magna</p></div>
    <div class="abs" style="left:178px;top:113px;width:95px"><p style="font-size:5.5px;font-weight:500">Title Goes Here</p><p class="body">Lorem ipsum dolor sit amet, consectetuer adipiscing elit, sed diam nonummy nibh euismod tincidunt ut laoreet dolore magna</p></div>
    <div class="footer"><div class="brand"><span class="dot"></span>Nivel Crest</div><div class="rule"></div><div class="page">NIVEL CREST | <b>01</b></div></div>
  </section>

  <!-- Closing -->
  <section class="slide" style="left:232px;top:925px">
    <div class="brand abs" style="left:10px;top:12px;font-size:8px"><span class="dot"></span>Nivel Crest</div>
    <div class="photo" style="left:0;top:32px;width:287px;height:123px" role="img" aria-label="Excavator at a construction site under a golden sky"></div>
    <h1 class="abs white" style="left:9px;top:43px;font-size:30px;font-weight:800;line-height:.98;letter-spacing:-.5px">THANK<br>YOU!</h1>
    <p class="abs white" style="left:10px;top:126px;font-size:12px;font-weight:700;line-height:1.05">PRESENTATION<br>TITLE GOES HERE</p>
  </section>

</main>
</body>
</html>
```